Need to drive pregnant women to my 3d4d ultrasound studio where i provide 4d ultrasound with hyperalistic imaging and gender reveals

Industry/Entity Type

Healthcare

Font styles to use
Decorative
Script

Requirements
Must have
• My Company name Cielo de Nuestra Espera 4D. EVERYTHING HAS TO BE IN SPANISH
Nice to have
• SIMPLE AND NOT TOO BUSY
Should not have
• website

```html
<!DOCTYPE html>
<html lang="es">
<head>
<meta charset="utf-8">
<title>Cielo de Nuestra Espera 4D — Valla</title>
<link rel="stylesheet" href="https://fonts.googleapis.com/css2?family=Russo+One&family=Urbanist:wght@500;800&display=swap">
<style>
  :root {
    --page-bg: #e9edf3;
    --navy-deep: #0c1d58;
    --navy: #12287a;
    --royal: #1f45b3;
    --heart-shadow: #0d1f5e;
    --white: #ffffff;
    --frame: #f4f6ef;
    --gold: #c9a45a;
    --orange: #e8892a;
  }
  * { margin: 0; padding: 0; box-sizing: border-box; }
  html, body { width: 1200px; height: 900px; overflow: hidden; }
  body { background: var(--page-bg); position: relative; }

  .billboard {
    position: absolute;
    left: 30px; top: 210px;
    width: 1140px; height: 480px;
    overflow: hidden;
    background:
      linear-gradient(100deg, var(--navy-deep) 0%, var(--navy) 14%, var(--royal) 24%, var(--navy) 36%, var(--navy-deep) 60%, var(--navy) 100%);
  }
  .billboard-art { position: absolute; inset: 0; }

  .headline {
    position: absolute;
    left: 48px; top: 52px;
    font-family: "Russo One", sans-serif;
    font-size: 84px;
    line-height: 0.94;
    color: var(--white);
    text-transform: uppercase;
    letter-spacing: 1px;
  }
  .contact {
    position: absolute;
    left: 50px; top: 376px;
    display: flex; align-items: center; gap: 14px;
    color: var(--white);
  }
  .contact-label {
    font-family: "Urbanist", sans-serif;
    font-weight: 500;
    font-size: 24px;
  }
  .contact-icon { width: 24px; height: 28px; }
  .contact-phone {
    font-family: "Urbanist", sans-serif;
    font-weight: 800;
    font-size: 42px;
    letter-spacing: 0.5px;
  }
</style>
</head>
<body>
  <section class="billboard">
    <svg class="billboard-art" viewBox="0 0 1140 480" width="1140" height="480">
      <defs>
        <path id="heart" d="M150 270 C60 200 0 140 0 80 C0 30 40 0 85 0 C115 0 140 20 150 45 C160 20 185 0 215 0 C260 0 300 30 300 80 C300 140 240 200 150 270 Z"/>
        <radialGradient id="scan-tone" cx="45%" cy="45%" r="70%">
          <stop offset="0" stop-color="#d98a3a"/>
          <stop offset="0.6" stop-color="#a85a1c"/>
          <stop offset="1" stop-color="#5e2c0c"/>
        </radialGradient>
        <radialGradient id="newborn-tone" cx="45%" cy="50%" r="70%">
          <stop offset="0" stop-color="#f4cdbd"/>
          <stop offset="0.7" stop-color="#e3a993"/>
          <stop offset="1" stop-color="#c98672"/>
        </radialGradient>
        <path id="star" d="M0 -10 L2.9 -3.1 L9.5 -3.1 L4.2 1.4 L5.9 8.1 L0 4.3 L-5.9 8.1 L-4.2 1.4 L-9.5 -3.1 L-2.9 -3.1 Z" fill="none" stroke="var(--gold)" stroke-width="1.8" stroke-linejoin="round"/>
      </defs>

      <g fill="var(--heart-shadow)">
        <use href="#heart" transform="translate(520 40) rotate(-8 150 135) scale(1.22)"/>
        <use href="#heart" transform="translate(780 50) rotate(8 150 135) scale(1.22)"/>
      </g>

      <g role="img" aria-label="Imagen de ecografía 4D de un bebé en el vientre, en tonos ámbar">
        <use href="#heart" transform="translate(570 80) rotate(-10 150 135)" fill="url(#scan-tone)" stroke="var(--frame)" stroke-width="9"/>
      </g>
      <g role="img" aria-label="Fotografía de un recién nacido dormido">
        <use href="#heart" transform="translate(820 95) rotate(10 150 135) scale(1.05)" fill="url(#newborn-tone)" stroke="var(--frame)" stroke-width="9"/>
      </g>

      <g class="stars">
        <use href="#star" transform="translate(570 150) scale(1.1)"/>
        <use href="#star" transform="translate(660 140) scale(1.1)"/>
        <use href="#star" transform="translate(620 190) scale(1.4)"/>
        <use href="#star" transform="translate(1065 230) scale(1.1)"/>
        <use href="#star" transform="translate(1110 245) scale(1.3)"/>
        <use href="#star" transform="translate(1115 300) scale(1)"/>
        <use href="#star" transform="translate(670 420) scale(1.1)"/>
        <use href="#star" transform="translate(830 410) scale(1.1)"/>
      </g>
    </svg>

    <h1 class="headline">Cielo de<br>Nuestra<br>Espera 4D</h1>

    <div class="contact">
      <span class="contact-label">Para orientación</span>
      <svg class="contact-icon" viewBox="0 0 24 28" aria-hidden="true">
        <path d="M6 2 L10 2 L11 9 L8 11 C9 15 11 18 14 20 L16 17 L22 19 L22 24 C22 26 20 27 18 26 C10 23 4 16 3 7 C3 4 4 2 6 2 Z" fill="var(--orange)"/>
      </svg>
      <span class="contact-phone">555-204-3187</span>
    </div>
  </section>
</body>
</html>
```